Buch-/eBook-Cover für Traumatherapeutin
Zielgruppe
Ich bin Traumatherapeutin und schreibe ein Buch zum Thema Trauma bearbeiten.
Meine Zielgruppe sucht Heilung, Genesung, Selbstliebe etc.
Aufgabenstellung
Buchcover
Bitte erstell mir ein modernes positives inspirierendes Buchcover mit dem
Titel: 'Morgenlicht NEU entdecken“
Untertitel: „Spüre den Mut der ganz in dir wohnt“
Dr. Mira Kessow
Ich hätte gerne ein modernes Buch, das entweder einen Bezug zum Thema Trauma hat oder aber einfach stylische Schriftzüge. Bin aber auch offen für andere Vorschläge.
Dunkelblau, weiß und türkis oder auch rosa mag ich ganz gerne. Wobei Dunkelblau, weiß und türkis meine Favoriten sind und mit rosa höchstens kleinere Akzente gesetzt werden sollten.
Das Buchcover soll modern sein und direkt ansprechen. Gerne eine originelle Lösung, oder etwas Besonderes, etwas das Tiefe ausdrückt, oder man mehrmals hinsehen muss um etwas zu erkennen oder etwas das mehr Interpretationsspielraum lässt.
Gerne auch viel weiß, zumindest heller und nicht zu dunkel. Stylish, aber nicht überfrachtet.
Schreib mich gerne an, wenn du Fragen hast.
Ich habe mal zwei Beispiel von Typolösungen angehängt, die ich ganz cool fände.
Ich freue mich auf deine Ideen :-)
Ganz liebe Grüße
Mira

```html
<!DOCTYPE html>
<html lang="de">
<head>
<meta charset="utf-8">
<title>Morgenlicht neu entdecken – Buchcover</title>
<link href="https://fonts.googleapis.com/css2?family=Source+Sans+3:wght@300;400;700;900&family=Great+Vibes&display=swap" rel="stylesheet">
<style>
  :root {
    --navy: #3f6aa0;
    --teal: #208ca8;
    --teal-soft: #5aa3b0;
    --sky-light: #eef5f9;
    --sky: #b9d8e8;
    --sky-deep: #9cc3d9;
    --band: rgba(255, 255, 255, 0.55);
    --dots: #ffffff;
  }
  * { margin: 0; padding: 0; box-sizing: border-box; }
  html, body { width: 846px; height: 1200px; overflow: hidden; background: #fff; }
  .cover {
    position: relative;
    width: 846px;
    height: 1200px;
    overflow: hidden;
    font-family: "Source Sans 3", "Source Sans Pro", sans-serif;
  }
  .cover__artwork {
    position: absolute;
    inset: 0;
    background:
      radial-gradient(ellipse 42% 55% at 50% 42%, rgba(255,255,255,0.95) 0%, rgba(240,244,247,0.7) 45%, rgba(255,255,255,0) 75%),
      radial-gradient(ellipse 60% 40% at 70% 80%, rgba(230,236,242,0.6) 0%, rgba(255,255,255,0) 70%),
      linear-gradient(160deg, var(--sky-light) 0%, #dcebf3 25%, var(--sky) 55%, #a9c9dc 80%, var(--sky-deep) 100%);
  }
  .band {
    position: absolute;
    left: 0;
    width: 100%;
    background: var(--band);
  }
  .band--author { top: 127px; height: 54px; }
  .band--subtitle { top: 895px; height: 133px; background: rgba(255,255,255,0.6); }
  .author {
    position: absolute;
    top: 127px;
    width: 100%;
    height: 54px;
    line-height: 54px;
    text-align: center;
    color: var(--navy);
    font-weight: 700;
    font-size: 39px;
    letter-spacing: 0.5px;
  }
  .title {
    position: absolute;
    top: 315px;
    width: 100%;
    text-align: center;
  }
  .title__line {
    display: block;
    color: var(--teal);
    font-weight: 900;
    text-transform: uppercase;
    line-height: 1;
  }
  .title__line--top { font-size: 96px; letter-spacing: 1px; }
  .title__accent {
    display: block;
    font-family: "Great Vibes", cursive;
    color: var(--navy);
    font-size: 160px;
    line-height: 0.9;
    margin: 10px 0 0;
  }
  .title__line--bottom { font-size: 110px; letter-spacing: 1px; margin-top: 4px; }
  .wave {
    position: absolute;
    left: 0;
    top: 745px;
    width: 846px;
    height: 110px;
  }
  .subtitle {
    position: absolute;
    top: 905px;
    left: 0;
    width: 100%;
    color: var(--teal-soft);
    font-weight: 400;
    font-size: 38px;
    line-height: 1.2;
  }
  .subtitle__first { display: block; padding-left: 160px; }
  .subtitle__script {
    font-family: "Great Vibes", cursive;
    font-size: 58px;
    line-height: 1;
  }
  .subtitle__second { display: block; padding-left: 392px; margin-top: 2px; }
</style>
</head>
<body>
<main class="cover">
  <div class="cover__artwork" role="img" aria-label="Zarte weiße Feder auf hellblauem, sanft verlaufendem Hintergrund"></div>

  <div class="band band--author"></div>
  <p class="author">DR. MIRA KESSOW</p>

  <h1 class="title">
    <span class="title__line title__line--top">Morgenlicht</span>
    <span class="title__accent">neu</span>
    <span class="title__line title__line--bottom">Entdecken</span>
  </h1>

  <svg class="wave" viewBox="0 0 846 110" aria-hidden="true">
    <path d="M0 95 C 120 20, 200 5, 300 25 S 480 95, 620 100 S 790 75, 846 50"
          fill="none" stroke="var(--dots)" stroke-width="3.2"
          stroke-linecap="round" stroke-dasharray="0.1 6.5"/>
  </svg>

  <div class="band band--subtitle"></div>
  <p class="subtitle">
    <span class="subtitle__first">Spüre den <span class="subtitle__script">Mut</span></span>
    <span class="subtitle__second">der ganz in dir wohnt</span>
  </p>
</main>
</body>
</html>
```